Community coffee table book/quiz book

I need a couple of things for my book:
- Book cover (Title: "1000 spørsmål om Kvernhaugen")
- "Cover pages" for each chapter of the book (15-16 chapters)
- "Watermark" or background design for all the pages of the book.
- A cover image for the book's Kretsbok page.
- Design of a paper "belt"

The book:
The book will consist of about 200+ pages with ten questions on one page and ten answers on the next.

The name of the book is "1000 spørsmål om Kvernhaugen" which means 1000 questions about Kvernhaugen (Kvernhaugen is a suburb of the city Bergen in Norway). Author is Helge Myrvold.
The questions in the book are grouped in chapters like:
History
Facts
Schools
Businesses
People/profiles
Sport
Culture
Buildings/Landmarks/Sculptures
The different areas of the suburb
The city
Language/expressions
Nature
The names of the chapters are not set, so it would be good to have the option to change the title of the pages without having to contact the designer (maybe by adding the text on top of the cover page?). I therefore suggest that these images are without text.
The book size is 18X18 cm.

The chapter cover pages:
The book will basically consist of text. Ten questions on one page, and ten questions on the next. Visually it will be quite "boring" to look at. I would therefore like to have a chapter cover page for each chapter, preferable in colour.

Water mark:
To avoid having a book full of white pages with limited amount of text I thought of having some kind of design on each page. I do not know how this should be done, but maybe it is possible to create some kind of background image or watermark image with similar design as the book cover and the chapter covers?

The Kretsbok cover image:
This should be the same as, or similar to, the book cover.
I believe the optimal size is 828px x 315px?

Paper "belt":
The book is to be sold for charity. The receiver of the money is the local sports club. I would like to have the book "wrapped in a 5-6 cm wide paper belt with the logo of the sports club (please see logo and colours here: http://www.ilbrattlia.no). I do not think that the book cover itself should have the sports club's color (purple), but maybe the paper band could? (Again: YOU are the designer)

Photos:
I reckon you would like some photos for both the book cover and the chapter covers. I will of course do the best I can to provide these photos when I have selected a designer. I the meantime

Target Market(s)

Target market is middle clas men and women 35+ from the geographical area Kvernhaugen.

Industry/Entity Type

Community

Font styles to use
Serif
Sans Serif

Requirements
Must have
• The book will be sold by children on doors. The buyers will probably take a look briefly through the book and then decide if they are going to buy.
• It is important that they like the question types, categories and some of the actual questions they read. But it is also important that they like the look of the book. Therefore the book cover and the chapter cover pages must be appealing enough for the buyers to want this book on theor coffee table.
Nice to have
• I have uploaded a short video clip to Vidtrekk (https://www.vidtrekk.example/watch?v=qx7Ta2Lm9pz). This a promo clip from Pimlo Kanalen. I felt inspired when I saw it and thought that backgrounds like the ones used in the promo could also be used as backgrounds for each chapter's cover pages. Maybe different colour for each chapter? Screenshots from the clip is uploaded below.
• Then again: Maybe I am an idiot? YOU are the designer :-)
Should not have
• There has been some rivalry between two sportsclubs in the region after the clubs was merged a couple of years ago. I therefore believe we should therefore try avoid both the old clubs' colours (blue&yellow and green) and the new club's colour (purple).

```html
<!DOCTYPE html>
<html lang="no">
<head>
<meta charset="utf-8">
<title>1000 quizgåter om Kvernhaugen – bokomslag</title>
<link rel="stylesheet" href="https://fonts.googleapis.com/css2?family=Archivo+Black&family=Playfair+Display:ital,wght@1,700&family=Poppins:wght@400;700&family=PT+Sans+Narrow&display=swap">
<style>
  :root {
    --page: #ffffff;
    --cover-orange: #f05a24;
    --band-amber: #f7a11a;
    --block-yellow: #fdb714;
    --edge-yellow: #fdd14c;
    --ink: #1b1b1b;
    --paper-white: #ffffff;
  }
  html, body {
    margin: 0;
    padding: 0;
    width: 1200px;
    height: 1000px;
    overflow: hidden;
    background: var(--page);
  }
  .artboard {
    position: relative;
    width: 1200px;
    height: 1000px;
  }
  .cover-art {
    position: absolute;
    inset: 0;
    width: 1200px;
    height: 1000px;
  }
  .cover-edge { fill: var(--edge-yellow); }
  .cover-face { fill: var(--cover-orange); }
  .cover-band { fill: var(--band-amber); }
  .corner-block { fill: var(--block-yellow); }
  .title-panel { fill: var(--block-yellow); }
  .title-panel-shade { fill: var(--band-amber); }
  .title-number {
    font-family: "Archivo Black", sans-serif;
    fill: var(--ink);
  }
  .title-word {
    font-family: "Playfair Display", serif;
    font-style: italic;
    font-weight: 700;
    fill: var(--paper-white);
  }
  .title-joiner {
    font-family: "Poppins", sans-serif;
    font-weight: 400;
    fill: var(--paper-white);
  }
  .author-name {
    font-family: "Poppins", sans-serif;
    font-weight: 700;
    fill: var(--ink);
  }
  .sheet-label {
    position: absolute;
    left: 0;
    width: 1200px;
    top: 838px;
    margin: 0;
    text-align: center;
    font-family: "PT Sans Narrow", "Arial Narrow", sans-serif;
    font-weight: 400;
    font-size: 104px;
    line-height: 1;
    color: #000;
  }
</style>
</head>
<body>
<main class="artboard">
  <svg class="cover-art" viewBox="0 0 1200 1000" xmlns="http://www.w3.org/2000/svg" aria-labelledby="cover-title">
    <title id="cover-title">1000 quizgåter om Kvernhaugen – Helge Myrvold</title>

    <g class="cover-base">
      <rect class="cover-edge" x="266" y="51" width="736" height="748"/>
      <rect class="cover-face" x="262" y="55" width="736" height="740"/>
      <rect class="cover-band" x="262" y="55" width="736" height="66"/>
      <rect class="cover-band" x="262" y="728" width="736" height="67"/>
      <rect class="corner-block" x="880" y="121" width="118" height="34"/>
      <rect class="corner-block" x="262" y="694" width="118" height="34"/>
    </g>

    <g class="title-backdrop">
      <rect class="title-panel-shade" x="410" y="262" width="460" height="128"/>
      <rect class="title-panel" x="400" y="252" width="480" height="118"/>
      <rect class="title-panel-shade" x="400" y="402" width="470" height="44"/>
    </g>

    <g class="cover-title">
      <text class="title-number" x="440" y="380" font-size="175" textLength="392" lengthAdjust="spacingAndGlyphs">1000</text>
      <text class="title-word" x="410" y="462" font-size="84" textLength="448" lengthAdjust="spacingAndGlyphs">Quizgåter</text>
      <text class="title-joiner" x="775" y="504" font-size="36" textLength="56" lengthAdjust="spacingAndGlyphs">om</text>
      <text class="title-word" x="490" y="572" font-size="70" textLength="366" lengthAdjust="spacingAndGlyphs">Kvernhaugen</text>
      <text class="author-name" x="581" y="609" font-size="13" textLength="118" lengthAdjust="spacingAndGlyphs">Helge Myrvold</text>
    </g>
  </svg>

  <p class="sheet-label">BOOK COVER</p>
</main>
</body>
</html>
```